Business Card Design

Hi I need a business card designed, we already have the business name logo artwork and would like some concept ideas for the Bus Card layout.
On the back of the card i want to include the products and services that we offer.
We are a Plastics Sheeting manufacture based in Perth Australia.

                                       

We need a BC design for a company called Tarvo Plastics based in Perth Australia.

We supply from DIY to Trade & Industrial  Engineering Markets.

We specialise in:

·         Cut to size panels  (all shapes and sizes)

·         Plastics fabrication & Welding

·         Custom Designs

·         Plastic Repairs

·         PVC Pipe Slotting & PVC Pipe Threading

·         Supplier of all types of engineering plastics and profiles.

Including:           Acrylic / Clarvene

                               Polycarbonate / Dorvil

                               Prismatic Light Diffuser

                               Vantrib

                               HDPE / UHMWPE

                               PVC / PVC Foam

                               Nylon

                               HIPS

```html
<!DOCTYPE html>
<html lang="en">
<head>
<meta charset="utf-8">
<title>Tarvo Plastics – Business Card</title>
<link rel="stylesheet" href="https://fonts.googleapis.com/css2?family=Ubuntu:wght@400;500;700&display=swap">
<style>
  :root {
    --navy: #13285e;
    --blue: #2a8fd0;
    --sky: #8cc6ea;
    --orange: #ec7a1c;
    --red: #c8202f;
    --grey: #4a4f5c;
    --paper: #ffffff;
    --backdrop: #e9e7e3;
  }
  * { box-sizing: border-box; margin: 0; padding: 0; }
  html, body { width: 1200px; height: 720px; overflow: hidden; }
  body {
    background: var(--backdrop);
    font-family: "Ubuntu", sans-serif;
    position: relative;
  }
  .card {
    position: absolute;
    top: 189px;
    width: 560px;
    height: 342px;
    background: var(--paper);
    overflow: hidden;
    box-shadow: 0 4px 14px rgba(0,0,0,.18);
  }
  .card--front { left: 26px; }
  .card--back { left: 614px; }

  .front-art { position: absolute; inset: 0; }

  .brand {
    position: absolute;
    left: 36px;
    top: 44px;
    display: flex;
    align-items: center;
    gap: 12px;
  }
  .brand-mark { width: 22px; height: 22px; background: var(--navy); }
  .brand-name {
    font-size: 46px;
    font-weight: 700;
    color: var(--navy);
    letter-spacing: -0.5px;
  }

  .person { position: absolute; left: 40px; top: 170px; color: var(--grey); }
  .person-name { font-size: 17px; font-weight: 700; color: var(--navy); margin-bottom: 10px; }
  .person-title { color: var(--orange); font-weight: 500; font-size: 14px; }
  .person-entity { font-size: 12px; line-height: 1.35; }

  .contacts {
    position: absolute;
    right: 26px;
    top: 78px;
    list-style: none;
    color: #fff;
    font-size: 13px;
    text-align: right;
  }
  .contacts li { display: flex; justify-content: flex-end; align-items: center; gap: 6px; height: 20px; }
  .contacts li.email { margin-top: 6px; }
  .contacts svg { width: 12px; height: 12px; fill: #fff; }

  .address {
    position: absolute;
    right: 26px;
    top: 222px;
    color: #fff;
    font-size: 13.5px;
    line-height: 1.45;
    text-align: right;
  }

  .back-content {
    position: absolute;
    inset: 0;
    display: flex;
    flex-direction: column;
    align-items: center;
    padding-top: 30px;
    color: var(--navy);
    text-align: center;
  }
  .offer-heading { font-size: 15px; font-weight: 700; line-height: 1.3; }
  .section-title { font-size: 19px; font-weight: 700; margin: 14px 0 6px; }
  .bullet-list {
    list-style: none;
    font-size: 13px;
    line-height: 1.55;
    color: var(--navy);
  }
  .bullet-list span { white-space: nowrap; margin: 0 4px; }
  .bullet-list span::before {
    content: "";
    display: inline-block;
    width: 6px; height: 6px;
    border-radius: 50%;
    background: var(--blue);
    margin-right: 5px;
    vertical-align: middle;
  }
</style>
</head>
<body>

<section class="card card--front">
  <svg class="front-art" viewBox="0 0 560 342" aria-hidden="true">
    <path d="M0,308 C170,312 250,235 330,160 C400,95 470,52 560,38 L560,342 L0,342 Z" fill="var(--navy)"/>
    <path d="M300,150 C370,80 450,28 560,8 L560,24 C460,40 390,84 318,150 Z" fill="var(--orange)"/>
    <path d="M0,282 C160,292 250,225 325,150" fill="none" stroke="var(--blue)" stroke-width="7"/>
    <path d="M0,268 C170,278 255,205 330,135" fill="none" stroke="var(--sky)" stroke-width="3"/>
    <path d="M0,322 C180,326 270,250 350,175" fill="none" stroke="#fff" stroke-width="3" opacity=".85"/>
  </svg>

  <div class="brand">
    <span class="brand-mark"></span>
    <span class="brand-name">Tarvo Plastics</span>
  </div>

  <div class="person">
    <p class="person-name">Your Name, <span class="person-title">Title</span></p>
    <p class="person-entity">Tarvo Holdings Pty Ltd<br>T/A Tarvo Plastics ABN: TBA</p>
  </div>

  <ul class="contacts">
    <li><svg viewBox="0 0 12 12"><path d="M2 1h3l1 3-1.5 1a7 7 0 0 0 2.5 2.5L8 6l3 1v3a1 1 0 0 1-1 1A9 9 0 0 1 1 2a1 1 0 0 1 1-1z"/></svg>08 9470 3115</li>
    <li><svg viewBox="0 0 12 12"><path d="M3 0h6a1 1 0 0 1 1 1v10a1 1 0 0 1-1 1H3a1 1 0 0 1-1-1V1a1 1 0 0 1 1-1zm0 2v7h6V2zm3 8a.7.7 0 1 0 0 1.4A.7.7 0 0 0 6 10z"/></svg>0400 555 123</li>
    <li><svg viewBox="0 0 12 12"><path d="M3 0h5v3H3zM1 4h10v6H1zm2 2v1h6V6z"/></svg>08 9470 3116</li>
    <li class="email"><svg viewBox="0 0 12 12"><path d="M0 2h12v8H0zm1 1v.4l5 3.2 5-3.2V3z"/></svg>sales@tarvoplastics.com.au</li>
  </ul>

  <p class="address">Unit 4/18 Keelan Road Westmere WA 6159<br>PO Box 2284 Westmere DC WA 6974</p>
</section>

<section class="card card--back">
  <div class="back-content">
    <h2 class="offer-heading">The Products And Services That We Offer<br>Are Supplied From Diy To Trade &amp; Industrial Engineering Markets</h2>

    <h3 class="section-title">We specialise in:</h3>
    <ul class="bullet-list">
      <li><span>Cut to size panels (all shapes and sizes)</span><span>Custom Designs</span></li>
      <li><span>Plastics fabrication &amp; Welding</span><span>PVC Pipe Slotting &amp; PVC Pipe Threading</span></li>
      <li><span>Plastic Repairs</span><span>Supplier of all types of engineering plastics and profiles</span></li>
    </ul>

    <h3 class="section-title">Including:</h3>
    <ul class="bullet-list">
      <li><span>Acrylic / Clarvene</span><span>Polycarbonate / Dorvil</span></li>
      <li><span>Prismatic Light Diffuser</span><span>Vantrib</span><span>HDPE / UHMWPE</span></li>
      <li><span>PVC / PVC Foam</span><span>Nylon</span><span>HIPS</span></li>
    </ul>
  </div>
</section>

</body>
</html>
```